Need Business Card ASAP

We need a business card design for a meeting coming up in a few days. The company name is Harlow Ridge Building and Construction and the logo is attached. Something clean, cool, and contemporary that we can get to a printer right away. Attached is the business card for Volmar Energy, an affiliated company, which we like. Instead of the hawk on the back, you could use the attached "D". We'll also be needing matching letterhead in the near future, so ideas for that are welcome.

```html
<!DOCTYPE html>
<html lang="en">
<head>
<meta charset="utf-8">
<title>Harlow Ridge Building and Construction – Business Card</title>
<link rel="stylesheet" href="https://fonts.googleapis.com/css2?family=Open+Sans:wght@400;600;700&display=swap">
<style>
  :root {
    --stage: #e9e6dc;
    --khaki-dark: #bdb78f;
    --khaki-light: #e4e2d2;
    --ink: #1f1f1f;
    --name-grey: #4a4840;
    --text-grey: #3a3a3a;
    --paper: #ffffff;
    --rule: #b9b9b9;
  }
  * { box-sizing: border-box; margin: 0; padding: 0; }
  html, body { width: 1034px; height: 1200px; overflow: hidden; }
  body {
    background: var(--stage);
    font-family: "Open Sans", Arial, sans-serif;
    position: relative;
  }

  /* Front of card */
  .card-front {
    position: absolute;
    left: 76px; top: 42px;
    width: 887px; height: 538px;
    background: var(--paper);
    box-shadow: 0 4px 14px rgba(0,0,0,0.25);
    overflow: hidden;
  }
  .title-band {
    height: 74px;
    background: linear-gradient(90deg, var(--khaki-dark), #d3cfb3 60%, var(--khaki-light));
    display: flex; align-items: center; justify-content: center;
    color: var(--name-grey);
    font-weight: 700;
    font-size: 30px;
    letter-spacing: 0.2px;
  }
  .title-band .job-title { font-size: 22px; margin-left: 6px; padding-top: 5px; }

  .brand-block {
    position: absolute;
    left: 159px; top: 155px;
    width: 184px; height: 233px;
  }
  .brand-square {
    height: 150px;
    background: linear-gradient(135deg, #aaa27a, #d8d5bd);
  }
  .brand-name {
    height: 83px;
    background: var(--ink);
    color: var(--khaki-dark);
    font-weight: 600;
    font-size: 17px;
    line-height: 1.2;
    text-align: center;
    display: flex; align-items: center; justify-content: center;
    padding: 0 10px;
  }

  .divider {
    position: absolute;
    left: 375px; top: 152px;
    width: 2px; height: 238px;
    background: linear-gradient(180deg, transparent, var(--rule) 20%, var(--rule) 80%, transparent);
  }

  .contact-list {
    position: absolute;
    left: 402px; top: 166px;
    list-style: none;
    color: var(--text-grey);
    font-size: 25px;
  }
  .contact-list li {
    display: flex; align-items: center;
    height: 56px;
  }
  .contact-list svg { width: 20px; height: 20px; margin-right: 10px; flex: none; }

  .company-band {
    position: absolute;
    left: 0; bottom: 0;
    width: 100%; height: 76px;
    background: var(--ink);
    color: var(--paper);
    text-align: center;
    padding-top: 6px;
  }
  .company-band .company { font-size: 28px; font-weight: 600; line-height: 1.2; }
  .company-band .address { font-size: 21px; line-height: 1.3; }

  /* Back of card */
  .card-back {
    position: absolute;
    left: 59px; top: 603px;
    width: 913px; height: 507px;
    background: linear-gradient(180deg, var(--khaki-dark), var(--khaki-light));
    box-shadow: 0 4px 14px rgba(0,0,0,0.25);
    display: flex; align-items: center; justify-content: center;
  }
  .card-back .back-name {
    color: var(--ink);
    font-weight: 600;
    font-size: 44px;
    text-align: center;
    line-height: 1.3;
  }
</style>
</head>
<body>

<section class="card-front">
  <header class="title-band">YOUR NAME,<span class="job-title">TITLE</span></header>

  <div class="brand-block">
    <div class="brand-square"></div>
    <div class="brand-name">Harlow Ridge Building &amp; Construction</div>
  </div>

  <div class="divider"></div>

  <ul class="contact-list">
    <li>
      <svg viewBox="0 0 20 20"><circle cx="10" cy="10" r="8.5" fill="none" stroke="#3a3a3a" stroke-width="1.4"/><path d="M7 5.5c-.8.6-1.2 1.6-.6 3 .8 2 2.4 3.8 4.4 4.8 1.2.6 2.2.2 2.8-.6l-1.6-1.4-1 .6c-1-.5-2-1.5-2.5-2.6l.6-1z" fill="#3a3a3a"/></svg>
      (123) 456-7890
    </li>
    <li>
      <svg viewBox="0 0 20 20"><rect x="5.5" y="1.5" width="9" height="17" rx="1.5" fill="none" stroke="#3a3a3a" stroke-width="1.5"/><rect x="7.5" y="4" width="5" height="6" fill="#3a3a3a"/><circle cx="10" cy="15" r="1.2" fill="#3a3a3a"/></svg>
      (123) 456-7890
    </li>
    <li>
      <svg viewBox="0 0 20 20"><path d="M2 8l8-5 8 5v8H2z" fill="#3a3a3a"/><path d="M2 8l8 5 8-5" fill="none" stroke="#fff" stroke-width="1.3"/></svg>
      yourname@harlowridge.com
    </li>
    <li>
      <svg viewBox="0 0 20 20"><g fill="none" stroke="#3a3a3a" stroke-width="1.4"><circle cx="10" cy="10" r="8"/><ellipse cx="10" cy="10" rx="3.5" ry="8"/><path d="M2 10h16M3.5 6h13M3.5 14h13"/></g></svg>
      www.harlowridge.com
    </li>
  </ul>

  <footer class="company-band">
    <div class="company">Harlow Ridge Building &amp; Construction</div>
    <div class="address">00, Complex Name, Street, City 00000</div>
  </footer>
</section>

<section class="card-back">
  <div class="back-name">Harlow Ridge<br>Building &amp; Construction</div>
</section>

</body>
</html>
```